Business Card Design

New business card design

Target Market(s)

Residential & Commercial Property Managers

Industry/Entity Type

Plumbing Services

Contact Information for Business Card

Name - Rowan Keddle, title - Director, Phone Number - 0431 286 517, email - rowan@tbk-plumbing.com.au, Company ABN - 73 215 904 386,

Font styles to use
Sans Serif

Colors
0054AA
0677BA
7BADD7
CADEEF
E8F1F8

```html
<!DOCTYPE html>
<html lang="en">
<head>
<meta charset="utf-8">
<title>TBK Plumbing Services – Business Card</title>
<link href="https://fonts.googleapis.com/css2?family=Lato:ital,wght@0,300;0,400;1,300&family=Montserrat:wght@500;700&display=swap" rel="stylesheet">
<style>
  :root {
    --stage: #232629;
    --card-light: #ffffff;
    --card-dark: #1d232a;
    --ink: #1b1f24;
    --ink-soft: #6d7177;
    --accent: #1b9ad6;
    --on-dark: #ffffff;
    --on-dark-soft: #c9ced4;
  }
  * { box-sizing: border-box; margin: 0; padding: 0; }
  html, body {
    width: 1200px; height: 952px; overflow: hidden;
    background: var(--stage);
  }
  .sheet {
    width: 1200px; height: 952px;
    display: flex; align-items: center; justify-content: center; gap: 48px;
  }
  .card {
    position: relative;
    width: 520px; height: 298px;
    overflow: hidden;
    box-shadow: 0 14px 34px rgba(0,0,0,.45);
  }
  /* Front */
  .card--front { background: var(--card-light); color: var(--ink); }
  .brand {
    font-family: "Lato", sans-serif;
    font-weight: 300;
    text-align: center;
    line-height: 1;
  }
  .card--front .brand {
    position: absolute; left: 120px; top: 44px; width: 220px;
    color: var(--ink);
  }
  .brand__name { display: block; font-size: 52px; letter-spacing: 2px; }
  .brand__tag { display: block; font-size: 9px; letter-spacing: 5px; margin-top: 8px; text-transform: lowercase; }
  .brand__dot {
    display: inline-block; width: 9px; height: 9px; border-radius: 50%;
    background: var(--accent); margin-left: 4px; vertical-align: baseline;
  }
  .contact {
    position: absolute; left: 44px; top: 160px;
    list-style: none;
    font-family: "Lato", sans-serif; font-size: 14px;
  }
  .contact__item { display: flex; align-items: center; gap: 9px; height: 24px; }
  .contact__item--muted { color: var(--ink-soft); font-weight: 300; font-style: italic; }
  .contact__icon { width: 17px; height: 17px; flex: none; }
  .contact__abn { font-weight: 400; color: var(--ink); }
  .contact__abn-label { color: var(--accent); }
  .person {
    position: absolute; right: 58px; top: 160px;
    text-align: right;
  }
  .person__name {
    font-family: "Montserrat", sans-serif; font-weight: 700;
    font-size: 22px; letter-spacing: .5px; text-transform: uppercase;
  }
  .person__name-first { font-weight: 500; }
  .person__role {
    font-family: "Lato", sans-serif; font-weight: 300;
    font-size: 15px; color: var(--ink-soft); margin-top: 2px;
  }
  .accent-block {
    position: absolute; right: 0; top: 206px;
    width: 42px; height: 36px; background: var(--accent);
  }
  /* Back */
  .card--back { background: var(--card-dark); display: flex; align-items: center; justify-content: center; }
  .card--back .brand { color: var(--on-dark); }
  .card--back .brand__name { font-size: 72px; letter-spacing: 3px; }
  .card--back .brand__tag { font-size: 10px; letter-spacing: 7px; margin-top: 12px; }
</style>
</head>
<body>
<main class="sheet">

  <section class="card card--front" aria-label="Business card front">
    <div class="brand">
      <span class="brand__name">tbk<span class="brand__dot"></span></span>
      <span class="brand__tag">plumbing services</span>
    </div>

    <ul class="contact">
      <li class="contact__item contact__item--muted">
        <svg class="contact__icon" viewBox="0 0 17 17" aria-hidden="true">
          <rect width="17" height="17" rx="2" fill="#1b1f24"/>
          <path d="M5 4c1 0 1.6 1.8 1.6 2.4S5.8 7.4 6 8c.5 1.2 1.6 2.3 2.9 2.9.6.2 1-.7 1.6-.7s2.4.6 2.4 1.6c0 .8-1 1.6-2 1.6C7.5 13.4 3.6 9.5 3.6 6 3.6 5 4.2 4 5 4z" fill="#fff"/>
        </svg>
        0431 286 517
      </li>
      <li class="contact__item contact__item--muted">
        <svg class="contact__icon" viewBox="0 0 17 17" aria-hidden="true">
          <rect width="17" height="17" rx="2" fill="#1b1f24"/>
          <rect x="3" y="5" width="11" height="8" fill="none" stroke="#fff" stroke-width="1.2"/>
          <path d="M3 5l5.5 4.5L14 5" fill="none" stroke="#fff" stroke-width="1.2"/>
        </svg>
        rowan@tbk-plumbing.com.au
      </li>
      <li class="contact__item contact__abn">
        <span class="contact__abn-label">ABN -</span>&nbsp;73 215 904 386
      </li>
    </ul>

    <div class="person">
      <p class="person__name"><span class="person__name-first">Rowan</span> Keddle</p>
      <p class="person__role">Director</p>
    </div>
    <div class="accent-block"></div>
  </section>

  <section class="card card--back" aria-label="Business card back">
    <div class="brand">
      <span class="brand__name">tbk<span class="brand__dot"></span></span>
      <span class="brand__tag">plumbing services</span>
    </div>
  </section>

</main>
</body>
</html>
```